Website redesign www.marigoldlawpc.com law firm site

Need to redesign the website that I currently have to look more modern and professional. Would also like to be able to make updates and post without having a huge hassle. See current www.marigoldlawpc.com. I just think that it looks very immature and it's very templated there's no ability for me to make posts or Add links or anything like that

Target Market(s)

California people looking for a powerhouse attorney in

Industry/Entity Type

Legal

Number of Pages Required

3 page

Font styles to use
Serif
Sans Serif

Colors
ec1f27
000000
ffffff

Requirements
Must have
• Must be mobile friendly. Must look professional and have ability to post links to other websites. Must have ability to post blogs or articles. Would like to be able to read my FeeTrove account and also have the ability to upload forms for people to download
Nice to have
• Simple design easy to use and not cluttered with too much text

```html
<!DOCTYPE html>
<html lang="en">
<head>
<meta charset="utf-8">
<title>Marigold Law P.C. – Chico California Attorney</title>
<link href="https://fonts.googleapis.com/css2?family=Raleway:wght@400;500;600;700&family=Open+Sans:wght@400;600;700&family=Playfair+Display:wght@600&display=swap" rel="stylesheet">
<style>
:root{
  --red:#ec1f27;
  --red-dark:#c8161d;
  --black:#000000;
  --ink:#222222;
  --text:#444444;
  --muted:#777777;
  --white:#ffffff;
  --grey-bg:#f4f4f4;
  --footer:#2b2b2b;
  --line:#e2e2e2;
}
*{margin:0;padding:0;box-sizing:border-box}
html,body{width:1200px;height:2707px;overflow:hidden;background:var(--white)}
body{position:relative;font-family:"Open Sans",Arial,sans-serif;color:var(--text)}
.abs{position:absolute}

/* header */
.site-header{top:0;left:0;width:1200px;height:78px;background:var(--white)}
.brand{left:160px;top:20px;font-family:"Playfair Display",Georgia,serif;font-weight:600;font-size:25px;color:var(--red-dark);letter-spacing:.5px}
.brand-rule{left:160px;top:56px;width:136px;height:1px;background:var(--red-dark)}
.main-nav{top:29px;left:386px;display:flex;gap:40px;font-family:"Raleway",Arial,sans-serif;font-size:13.5px;color:var(--ink)}
.main-nav .active{color:var(--red)}
.search-btn{left:1004px;top:21px;width:34px;height:34px;border-radius:50%;background:var(--red)}

/* hero */
.hero{top:78px;left:0;width:1200px;height:539px;background:linear-gradient(135deg,#4a4f57 0%,#2c3038 40%,#5c5f66 70%,#3a3d44 100%)}
.hero-shade{top:78px;left:0;width:1200px;height:539px;background:rgba(0,0,0,.25)}
.hero-title{top:272px;left:0;width:1200px;text-align:center;font-family:"Raleway",Arial,sans-serif;font-weight:700;font-size:38px;color:var(--white)}
.hero-sub{top:330px;left:0;width:1200px;text-align:center;font-family:"Raleway",Arial,sans-serif;font-weight:600;font-size:18px;line-height:24px;color:var(--white)}
.btn{background:var(--red);color:var(--white);font-family:"Raleway",Arial,sans-serif;font-weight:700;text-transform:uppercase;text-align:center}
.hero-btn{top:396px;left:524px;width:152px;height:38px;line-height:38px;font-size:12.5px}
.hero-dots{top:560px;left:570px;display:flex;gap:5px}
.hero-dots span{width:13px;height:13px;border-radius:50%;background:var(--white)}
.hero-dots span.on{background:transparent;border:2px solid var(--white)}

/* about */
.about-art{top:675px;left:160px;width:325px;height:220px;background:radial-gradient(ellipse at center,#a8141a 0%,#c9a78a 55%,#ffffff 80%)}
.about-title{top:655px;left:531px;font-family:"Raleway",Arial,sans-serif;font-weight:500;font-size:22px;line-height:32px;color:var(--black)}
.about-text{top:752px;left:535px;width:505px;font-size:11px;line-height:19.5px;color:var(--text)}

/* practice areas */
.practice{top:955px;left:0;width:1200px;height:457px;background:var(--red)}
.section-title{font-family:"Raleway",Arial,sans-serif;font-weight:500;font-size:23px;text-align:center;width:1200px;left:0}
.practice .section-title{top:0}
.practice-title{top:993px;color:var(--white)}
.practice-rule{top:1032px;left:490px;width:220px;height:1px;background:rgba(255,255,255,.6)}
.practice-intro{top:1043px;left:240px;width:720px;text-align:center;font-size:10.5px;line-height:20px;color:var(--white)}
.slider-arrow{top:1156px;width:22px;height:40px}
.area{top:1108px;width:200px;text-align:center;color:var(--white)}
.area-ring{margin:0 auto;width:134px;height:148px;position:relative}
.area-name{margin-top:8px;font-family:"Raleway",Arial,sans-serif;font-size:15px}
.area-desc{margin-top:14px;font-size:10.5px;line-height:19px}

/* firm columns */
.col-title{font-family:"Raleway",Arial,sans-serif;font-weight:600;font-size:22px;color:var(--black)}
.col-rule{height:2px;background:linear-gradient(90deg,var(--red) 0%,var(--red) 60%,rgba(236,31,39,.2) 100%)}
.col-photo{width:210px;height:175px;background:linear-gradient(160deg,#e6e8ec 0%,#9fa7b3 55%,#5d6570 100%)}
.col-text{width:185px;font-size:10.5px;line-height:19.5px;color:var(--text)}

/* blog */
.blog{top:1763px;left:0;width:1200px;height:538px;background:var(--grey-bg)}
.blog-title{top:1795px;color:var(--black)}
.blog-rule{top:1834px;left:530px;width:140px;height:2px;background:linear-gradient(90deg,rgba(236,31,39,.2),var(--red),rgba(236,31,39,.2))}
.post{top:1870px;width:208px;height:378px;background:var(--white);border:1px solid var(--line);box-shadow:0 1px 3px rgba(0,0,0,.08)}
.post-photo{height:152px}
.post-body{padding:14px 15px}
.post-title{font-family:"Raleway",Arial,sans-serif;font-size:16px;line-height:22px;color:var(--ink)}
.post-meta{margin-top:10px;font-size:9.5px;color:var(--red)}
.post-excerpt{margin-top:12px;font-size:10px;line-height:17px;color:var(--text)}
.post-btn{margin-top:18px;width:98px;height:34px;line-height:34px;font-size:10.5px}

/* partners */
.partners{top:2301px;left:0;width:1200px;height:102px;background:var(--white)}
.partner-name{font-family:"Raleway",Arial,sans-serif;font-weight:600;color:var(--ink)}

/* footer */
.footer{top:2403px;left:0;width:1200px;height:237px;background:var(--footer)}
.footer-brand{top:2446px;left:160px;width:200px;text-align:center;font-family:"Playfair Display",Georgia,serif;font-weight:600;font-size:28px;color:var(--white)}
.footer-about{top:2510px;left:160px;width:190px;font-size:10.5px;line-height:18px;color:#cccccc}
.footer-head{top:2446px;font-family:"Raleway",Arial,sans-serif;font-weight:700;font-size:14px;color:var(--white)}
.footer-list{top:2476px;list-style:none;font-size:11px;line-height:19.5px;color:#dddddd}
.footer-list li::before{content:"";display:inline-block;width:7px;height:7px;border-radius:50%;border:2px solid #dddddd;margin-right:7px;vertical-align:0}
.contact-row{left:808px;display:flex;gap:12px;font-size:10.5px;line-height:17px;color:#dddddd}
.contact-icon{width:24px;height:24px;border-radius:50%;border:1px solid #aaaaaa;flex:none}
.bottom-bar{top:2640px;left:0;width:1200px;height:67px;background:var(--red)}
.social{top:2658px;display:flex;gap:10px;left:162px}
.social span{width:28px;height:28px;border-radius:50%;border:1px solid rgba(255,255,255,.85)}
.copyright{top:2666px;left:784px;font-size:10.5px;color:var(--white)}
</style>
</head>
<body>

<header class="abs site-header">
  <div class="abs brand">Marigold Law P.C.</div>
  <div class="abs brand-rule"></div>
  <nav class="abs main-nav">
    <span class="active">Home</span><span>Attorney Profile</span><span>Practice Areas</span><span>Client Reviews</span><span>Links</span><span>Contact Us</span>
  </nav>
  <div class="abs search-btn">
    <svg width="34" height="34" viewBox="0 0 34 34"><circle cx="16" cy="16" r="5" fill="none" stroke="#fff" stroke-width="2"/><line x1="19.5" y1="19.5" x2="23" y2="23" stroke="#fff" stroke-width="2.2" stroke-linecap="round"/></svg>
  </div>
</header>

<section>
  <div class="abs hero" role="img" aria-label="Photo of attorneys and clients in a meeting around a conference table"></div>
  <div class="abs hero-shade"></div>
  <h1 class="abs hero-title">Welcome to Marigold Law</h1>
  <p class="abs hero-sub">Sed ut perspiciatis unde omnis iste natus sit voluptatem ac<br>cusantium dold ut perspiciatis unde omniorem.</p>
  <div class="abs btn hero-btn">Request a Quote</div>
  <div class="abs hero-dots"><span></span><span class="on"></span><span></span><span></span></div>
</section>

<section>
  <div class="abs about-art" role="img" aria-label="Word cloud illustration reading criminal law legal"></div>
  <h2 class="abs about-title">MARIGOLD LAW, P.C.<br>CHICO CALIFORNIA ATTORNEY</h2>
  <p class="abs about-text">Find the big firm style legal counsel you can work with in your hometown region at Marigold Law P.C., in Chico, CA. Attorney Dana L. Marigold, Esq., offers a boutique law firm opportunity for clients who want to enjoy all the advantages of her broad legal experience and education. She works closely with clients, and has the knowledge of many areas of law to apply to your situation. This is very helpful when it is necessary to incorporate those different areas of law practice into creating a winning argument for your unique case. Donec iaculis tempus magna, id rutrum sem commodo interdum. Interdum et malesuada fames ac ante ipsum primis in faucibunec iaculis tempus magna, id rutrum sem commodo interdum. Interdum et malesuada fames ac ante ipsum primis in faucibus.</p>
</section>

<section>
  <div class="abs practice"></div>
  <h2 class="abs section-title practice-title">PRACTICE AREAS</h2>
  <div class="abs practice-rule"></div>
  <p class="abs practice-intro">Sed ut perspiciatis unde omnis iste natus error sit voluptatem accusantium doloremque laudantium, totam rem aperiam, eaque ipsa quae ab illo inventore veritatis et quasi architecto beatae vitae dicta sunt explicabo enim ipsam voluptatem quia voluptas sit aspernatur</p>

  <svg class="abs slider-arrow" style="left:96px" viewBox="0 0 22 40"><polyline points="18,2 4,20 18,38" fill="none" stroke="#fff" stroke-width="1.6"/></svg>
  <svg class="abs slider-arrow" style="left:1092px" viewBox="0 0 22 40"><polyline points="4,2 18,20 4,38" fill="none" stroke="#fff" stroke-width="1.6"/></svg>

  <div class="abs area" style="left:158px">
    <div class="area-ring">
      <svg width="134" height="148" viewBox="0 0 134 148"><circle cx="67" cy="67" r="64" fill="#fff"/><circle cx="67" cy="67" r="55" fill="none" stroke="#ec1f27" stroke-width="2"/><polygon points="60,131 74,131 67,146" fill="#fff"/>
        <g fill="#ec1f27"><rect x="42" y="72" width="8" height="16"/><rect x="54" y="64" width="8" height="24"/><rect x="66" y="56" width="8" height="32"/><rect x="78" y="48" width="8" height="40"/></g>
        <polyline points="42,64 58,52 70,56 88,40" fill="none" stroke="#ec1f27" stroke-width="3"/><polygon points="82,38 92,36 90,46" fill="#ec1f27"/>
      </svg>
    </div>
    <div class="area-name">Business Law</div>
    <p class="area-desc">Sed ut perspiciatis unde omstusit voluptatem accusantium dolore ue lau dantium, totam rem aperiam.</p>
  </div>

  <div class="abs area" style="left:388px">
    <div class="area-ring">
      <svg width="134" height="148" viewBox="0 0 134 148"><circle cx="67" cy="67" r="64" fill="#fff"/><circle cx="67" cy="67" r="55" fill="none" stroke="#ec1f27" stroke-width="2"/><polygon points="60,131 74,131 67,146" fill="#fff"/>
        <polygon points="40,66 67,42 94,66 88,66 67,48 46,66" fill="#ec1f27"/><rect x="48" y="64" width="38" height="26" fill="#ec1f27"/><rect x="60" y="72" width="14" height="18" fill="#fff"/><rect x="78" y="44" width="6" height="12" fill="#ec1f27"/>
      </svg>
    </div>
    <div class="area-name">Real Estate Law</div>
    <p class="area-desc">Sed ut perspiciatis unde omstusit voluptatem accusantium dolore ue lau dantium, totam rem aperiam.</p>
  </div>

  <div class="abs area" style="left:618px">
    <div class="area-ring">
      <svg width="134" height="148" viewBox="0 0 134 148"><circle cx="67" cy="67" r="64" fill="#fff"/><circle cx="67" cy="67" r="55" fill="none" stroke="#ec1f27" stroke-width="2"/><polygon points="60,131 74,131 67,146" fill="#fff"/>
        <ellipse cx="66" cy="72" rx="24" ry="17" fill="#ec1f27"/><rect x="54" y="84" width="6" height="10" fill="#ec1f27"/><rect x="72" y="84" width="6" height="10" fill="#ec1f27"/><rect x="88" y="68" width="6" height="8" fill="#ec1f27"/>
        <circle cx="66" cy="46" r="9" fill="#ec1f27"/><circle cx="66" cy="46" r="4" fill="#fff"/>
      </svg>
    </div>
    <div class="area-name">Bankruptcy</div>
    <p class="area-desc">Sed ut perspiciatis unde omstusit voluptatem accusantium dolore ue lau dantium, totam rem aperiam.</p>
  </div>

  <div class="abs area" style="left:842px">
    <div class="area-ring">
      <svg width="134" height="148" viewBox="0 0 134 148"><circle cx="67" cy="67" r="64" fill="#fff"/><circle cx="67" cy="67" r="55" fill="none" stroke="#ec1f27" stroke-width="2"/><polygon points="60,131 74,131 67,146" fill="#fff"/>
        <g fill="#ec1f27"><circle cx="54" cy="52" r="8"/><circle cx="80" cy="52" r="8"/><path d="M40 80 q14 -24 28 0z"/><path d="M66 80 q14 -24 28 0z"/><circle cx="67" cy="66" r="7"/><path d="M53 92 q14 -22 28 0z"/></g>
      </svg>
    </div>
    <div class="area-name">Family Law</div>
    <p class="area-desc">Sed ut perspiciatis unde omstusit voluptatem accusantium dolore ue lau dantium, totam rem aperiam.</p>
  </div>
</section>

<section>
  <h2 class="abs col-title" style="top:1460px;left:160px">MARIGOLD LAW P.C.</h2>
  <div class="abs col-rule" style="top:1497px;left:160px;width:235px"></div>
  <div class="abs col-photo" style="top:1527px;left:162px" role="img" aria-label="Photo of business people meeting at a laptop"></div>
  <p class="abs col-text" style="top:1520px;left:389px">Marigold Law P.C. is owned by Dana L. Marigold, a dedicated and caring profe ssional who uses her broad range of skills as a California lawyer to bring consumers and business owners exceptionally strong legal repre sent ation that achieves best results. She wor ks with people from across the nort hern region of California Law &amp; Civil Litigation.</p>

  <h2 class="abs col-title" style="top:1460px;left:627px">CHICO CA LAW FIRM</h2>
  <div class="abs col-rule" style="top:1497px;left:627px;width:235px"></div>
  <div class="abs col-photo" style="top:1527px;left:629px" role="img" aria-label="Photo of an attorney advising clients at a desk"></div>
  <p class="abs col-text" style="top:1520px;left:857px">When you encounter challenges in your personal or business matters, call Attorney Dana L. Marigold to get the legal counsel you need to make important decisions. Our law firm approach is to work closely with clie nts to make sure they understand the legal process and related matters tha t apply to their case. Our attitude is that every client</p>
</section>

<section>
  <div class="abs blog"></div>
  <h2 class="abs section-title blog-title">LATEST BLOG NEWS</h2>
  <div class="abs blog-rule"></div>

  <article class="abs post" style="left:160px">
    <div class="post-photo" role="img" aria-label="Photo of a team meeting around a table" style="background:linear-gradient(150deg,#c9d3de,#6f7f93)"></div>
    <div class="post-body">
      <h3 class="post-title">Sed ut perspiciatis de omnis iste natus.</h3>
      <div class="post-meta">July 11,2016 &nbsp;&nbsp; Admin</div>
      <p class="post-excerpt">Sed ut perspiciatis unde omnis isa tus error sit voluptatem accusa ntiu mdoloremque laudantium.</p>
      <div class="btn post-btn">Read More</div>
    </div>
  </article>

  <article class="abs post" style="left:383px">
    <div class="post-photo" role="img" aria-label="Photo of a judge's gavel on a desk" style="background:linear-gradient(150deg,#d8c3a8,#7a5232)"></div>
    <div class="post-body">
      <h3 class="post-title">Sed ut perspiciatis de omnis iste natus.</h3>
      <div class="post-meta">July 11,2016 &nbsp;&nbsp; Admin</div>
      <p class="post-excerpt">Sed ut perspiciatis unde omnis isa tus error sit voluptatem accusa ntiu mdoloremque laudantium.</p>
      <div class="btn post-btn">Read More</div>
    </div>
  </article>

  <article class="abs post" style="left:606px">
    <div class="post-photo" role="img" aria-label="Photo of a professional working at a laptop" style="background:linear-gradient(150deg,#eeeeee,#9b9b9b)"></div>
    <div class="post-body">
      <h3 class="post-title">Sed ut perspiciatis de omnis iste natus.</h3>
      <div class="post-meta">July 11,2016 &nbsp;&nbsp; Admin</div>
      <p class="post-excerpt">Sed ut perspiciatis unde omnis isa tus error sit voluptatem accusa ntiu mdoloremque laudantium.</p>
      <div class="btn post-btn">Read More</div>
    </div>
  </article>

  <article class="abs post" style="left:829px">
    <div class="post-photo" role="img" aria-label="Photo of an attorney reading in a law library" style="background:linear-gradient(150deg,#b89a73,#3b2c22)"></div>
    <div class="post-body">
      <h3 class="post-title">Sed ut perspiciatis de omnis iste natus.</h3>
      <div class="post-meta">July 11,2016 &nbsp;&nbsp; Admin</div>
      <p class="post-excerpt">Sed ut perspiciatis unde omnis isa tus error sit voluptatem accusa ntiu mdoloremque laudantium.</p>
      <div class="btn post-btn">Read More</div>
    </div>
  </article>
</section>

<section>
  <div class="abs partners"></div>
  <svg class="abs" style="top:2326px;left:366px" width="54" height="54" viewBox="0 0 54 54" role="img" aria-label="Partner rating badge"><circle cx="27" cy="27" r="25" fill="#1f3f7a"/></svg>
  <svg class="abs" style="top:2326px;left:460px" width="54" height="54" viewBox="0 0 54 54" role="img" aria-label="State bar seal"><circle cx="27" cy="27" r="25" fill="none" stroke="#555" stroke-width="2"/></svg>
  <div class="abs partner-name" style="top:2342px;left:546px;font-size:16px;color:#34508a">CounselIndex</div>
  <div class="abs partner-name" style="top:2338px;left:686px;font-size:20px">NorthRidge Holdings</div>
</section>

<footer>
  <div class="abs footer"></div>
  <div class="abs footer-brand">Marigold Law</div>
  <p class="abs footer-about">Sed ut perspiciatis unde omnis iste natus error sit voluptatem accu san tium doloremque laudantium, totam rem aperiam, eaque ipsa qu</p>

  <h4 class="abs footer-head" style="left:437px">MENU</h4>
  <ul class="abs footer-list" style="left:438px">
    <li>Home</li><li>Attorney Profile</li><li>Practice Areas</li><li>Client Reviews</li><li>Links</li><li>Contact Us</li>
  </ul>

  <h4 class="abs footer-head" style="left:620px">LINKS</h4>
  <ul class="abs footer-list" style="left:621px">
    <li>Business Law</li><li>Real Estate Law</li><li>Bankruptcy</li><li>Family Law</li><li>Criminal Law</li><li>Civil Litigation</li><li>Unlawful Detainer</li>
  </ul>

  <h4 class="abs footer-head" style="left:808px">CONTACT US</h4>
  <div class="abs contact-row" style="top:2474px"><span class="contact-icon"></span><span style="padding-top:3px">Call Us (530) 555-0148</span></div>
  <div class="abs contact-row" style="top:2506px"><span class="contact-icon"></span><span>Marigold Law, P.C. Office 482 Orchard Lane,<br>Suite 310 Chico, CA 95926</span></div>
  <div class="abs contact-row" style="top:2552px"><span class="contact-icon"></span><span style="padding-top:3px">Fax: (888) 555-0173</span></div>
  <div class="abs contact-row" style="top:2582px"><span class="contact-icon"></span><span style="padding-top:3px">Email:dana@marigoldlawgroup.com</span></div>

  <div class="abs bottom-bar"></div>
  <div class="abs social"><span></span><span></span><span></span><span></span></div>
  <div class="abs copyright">© 2016 Marigold Law, P.C.. All copyrights are reserved.</div>
</footer>

</body>
</html>
```